July 2022 Industrial Manufacturer Product Expo Mexico City

We manufacture large screws and fastners for large Mining equipment, Trains, large ships, airplanes, wind turbines, and so on. We also do custom work base on the customer needs. No matter the size we can make it.
We have a Expo coming up with companies all over the world. We have to stand out we are a family own business so our customer service will be above and beyond anyone can provide. We do not have a sales force to push our products and services we provide one on one service.
Plus@!! I'm looking for anything that you designers can come up with if it was your company to put on a business card, plus i want to do a 1 or 2 sided pamphlet, and then a website. We make Speciality Bolts for large mining equipment these bolts can be 3 to 4 foot long!!! Plus fasteners, Nuts, washers, any, size, strengths, special materials, we offer more of a ono on one customer service, We are a small company, family own, but can fulfill any type of orders. We can also provide special time lines for emergency orders. "We keep the machines running we here at KRV don't believe in down time" We want to hear any slogan based on our company to stand out.
Thanks i really appreciate all your work and options that we have to pick on. Plus just a thought we could possibly want to entertain a experience Marketing internet help maybe a employment possibility. Thanks

I need 2 cards one in Spanish and English Like the steel back ground maybe send me in some bright red and blue writing Same with the Black cards Please remove the word Military The logo KRV maybe integrate a picture of a Bolt 🔩 Thank you

Still looking for I need 2 cards one in Spanish and English Like the steel back ground maybe send me in some bright red and blue writing Same with the Black cards try bright writing Please remove the word Military The logo KRV maybe integrate a picture of a Bolt 🔩 Plus will need the company to make a brochure and website next Thank you

Target Market(s)

Large Mining, Ship, Train, Green Energy, VELM, and Government equipment. Throughout the World

Industry/Entity Type

We can Custom Manufacture any type of Fastners for Mining equipment, Trains, Ships, Green energy, Governments, or military projects. wind turbines,

Contact Information for Business Card

I attached the name and contact info that's on a card, plus the Company Logo. Would like industrial looking background with Bright Colors that will stand out!! If we can insert somewhere maybe on back that we "Custom Manufacture Any Size or Quantity Fastners for Large Mining Equipment, Trains, Ships, Green Energy Equipment or Government Projects

Font styles to use
Other font styles liked:
• You Pick, has to be bold, colorful standout, Professional looking Beable to read it.

Colors

Designer to choose colors to be used in the design.

Requirements
Must have
• Need in Spanish and English TO STANDOUT FROM THE REST OF THE EXPO!! See Business card details, Rounded corners
Nice to have
• Can i see some of the darker cards with Bright Red and Blue letters I like to see the different type of card material, heavy thickness, plastic, transparent, Metal types, Bright Colors, I saw like Raised letters like on the logo.

```html
<!DOCTYPE html>
<html lang="es">
<head>
<meta charset="utf-8">
<title>KRV Business Card</title>
<link rel="stylesheet" href="https://fonts.googleapis.com/css2?family=Tinos:wght@400;700&display=swap">
<style>
  :root {
    --bg: #2b2b2b;
    --card-dark: #000000;
    --card-sheen: #5e5e60;
    --ink-light: #ffffff;
    --ink-red: #ff3a3a;
    --ink-blue: #3d9bff;
    --mark-grey: #9a9a9c;
    --mark-blue: #1a5fc0;
    --arc-blue: #0a3f9e;
    --paper: #ffffff;
  }
  * { box-sizing: border-box; margin: 0; padding: 0; }
  html, body {
    width: 1200px;
    height: 1015px;
    overflow: hidden;
    background: var(--bg);
    font-family: "Tinos", "Times New Roman", serif;
  }
  .canvas { position: relative; width: 1200px; height: 1015px; }
  .card {
    position: absolute;
    left: 320px;
    width: 560px;
    height: 320px;
    border-radius: 10px;
    overflow: hidden;
    box-shadow: 0 14px 30px rgba(0,0,0,0.55);
  }
  .card-back { top: 150px; background: linear-gradient(160deg, var(--card-sheen) 0%, #1a1a1a 45%, var(--card-dark) 80%); }
  .card-front { top: 530px; background: linear-gradient(160deg, #6a6a6c 0%, #1b1b1b 40%, var(--card-dark) 75%); }
  .card-art { position: absolute; inset: 0; width: 100%; height: 100%; }

  .brand-mark {
    position: absolute;
    display: flex;
    align-items: center;
    gap: 14px;
    font-weight: 700;
    letter-spacing: 10px;
    line-height: 1;
  }
  .brand-dot { border-radius: 50%; }
  .card-back .brand-mark {
    top: 58px; left: 0; right: 0; justify-content: center;
    font-size: 68px; color: var(--mark-grey);
  }
  .card-back .brand-dot { width: 16px; height: 16px; background: var(--mark-grey); }
  .tagline {
    position: absolute;
    left: 36px; right: 36px;
    text-align: center;
    font-size: 15px;
    line-height: 1.3;
  }
  .tagline-en { top: 168px; color: var(--ink-red); }
  .tagline-es { top: 236px; color: var(--ink-blue); }

  .card-front .brand-mark {
    top: 124px; left: 345px;
    font-size: 58px; color: var(--mark-blue);
  }
  .card-front .brand-dot { width: 14px; height: 14px; background: var(--mark-blue); }
  .holder-name {
    position: absolute; left: 34px; top: 40px;
    color: var(--ink-light); font-size: 22px; font-weight: 400;
  }
  .quote-label, .quote-email {
    position: absolute; left: 46px; font-size: 16px;
  }
  .quote-label { top: 90px; color: var(--ink-red); }
  .quote-email { top: 110px; color: var(--ink-blue); }
  .phone-list {
    position: absolute; left: 46px; bottom: 34px;
    list-style: none; color: var(--ink-light); font-size: 17px;
  }
  .phone-list li { display: flex; align-items: center; gap: 8px; line-height: 1.35; }
  .phone-list svg { width: 14px; height: 14px; }
</style>
</head>
<body>
<main class="canvas">

  <section class="card card-back" aria-label="Reverso de la tarjeta">
    <div class="brand-mark"><span class="brand-dot"></span>KRV</div>
    <p class="tagline tagline-en" lang="en">
      Custom Manufacture Any Size or Quantity Fastners for Large<br>
      Mining Equipment, Trains, Ships, Green Energy Equipment<br>
      or Government Projects
    </p>
    <p class="tagline tagline-es">
      Fabricación a medida de tornillería de cualquier tamaño o cantidad<br>
      para equipo minero, trenes, barcos, energía verde<br>
      o proyectos de gobierno
    </p>
  </section>

  <section class="card card-front" aria-label="Frente de la tarjeta">
    <svg class="card-art" viewBox="0 0 560 320" preserveAspectRatio="none" aria-hidden="true">
      <path d="M560 0 L330 0 A205 205 0 0 0 430 320 L560 320 Z" fill="var(--paper)"/>
      <path d="M345 30 A185 185 0 0 0 450 300" fill="none" stroke="var(--arc-blue)" stroke-width="3"/>
    </svg>
    <div class="brand-mark"><span class="brand-dot"></span>KRV</div>
    <h1 class="holder-name">Lic. Mariana Solis Vega</h1>
    <p class="quote-label">Cotizaciones en</p>
    <p class="quote-email">ventas.krvfijaciones@correo.mx</p>
    <ul class="phone-list">
      <li>
        <svg viewBox="0 0 16 16" aria-hidden="true"><path d="M3 1.5 L6 1.5 L7 5 L5.2 6.3 A8 8 0 0 0 9.7 10.8 L11 9 L14.5 10 L14.5 13 A1.5 1.5 0 0 1 13 14.5 A11.5 11.5 0 0 1 1.5 3 A1.5 1.5 0 0 1 3 1.5 Z" fill="var(--ink-light)"/></svg>
        5550193601
      </li>
      <li>
        <svg viewBox="0 0 16 16" aria-hidden="true"><rect x="4" y="1" width="8" height="14" rx="1.5" fill="none" stroke="var(--ink-light)" stroke-width="1.5"/><circle cx="8" cy="12.5" r="0.9" fill="var(--ink-light)"/></svg>
        5550127600
      </li>
    </ul>
  </section>

</main>
</body>
</html>
```